Website for Reiki and Wellness Courses

I teach online courses in Reiki and wellness/self-development and am needing a new website.

The focus of the website will be to provide descriptions of the courses as well as include a blog and pages where students in my courses will visit for additional information.

Note: courses are NOT hosted on this site.
The focus of this website will be to encourage viewers to enroll in courses as well as opt in to the email list.

I will upload copy soon. My old website is: http://brightfernstudies.example. Please do not use existing logo.

Target Market(s)

Alternative health, wellness, spirituality, personal development. Males and females of all ages seeking to improve their health and life.

Industry/Entity Type

Health And Wellness

Logo Text

No text (please do not use existing logo)

Coding

Coded - Design and coding required

Number of Pages Required

5+ page

Requirements
Must have
• 1. Home page
• 2. About page
• 3. Courses page that outlines courses (there are currently 6 courses with 1 coming soon)
• 4. Individual course page (maybe a template that I can adjust color and pictures for with each course)
• 5. Blog
• 6. Student Area that outlines all Student Areas
• 7. Individual Student Area page (maybe a template that I can adjust color and pictures for with each course)
• 8. Shop page (note: items will not currently be purchased through website - it will be a link to quillmarket for a book).
• 9. Student thank-you page (maybe a template that I can adjust color and pictures for with each course) this is the page students are directed to at end of course with vouchers for other courses.
• Opt-in for the home page, course pages, blog and thank-you pages
Nice to have
• I would like the design to be calm, clean and soothing. Ideally visitors feel relaxed when viewing the site and are encouraged to explore the courses, subscribe to the email list and purchase a product.
• ~ Testimonials page
• ~ Contact page
• I tend to gravitate towards blues, greys and purples as well as monochromatic color schemes.
Should not have
• Contact form on home page
• phone number on home page
• location/physical address
• dates for blog posts

```html
<!DOCTYPE html>
<html lang="en">
<head>
<meta charset="utf-8">
<title>Bright Fern Studies</title>
<link href="https://fonts.googleapis.com/css2?family=Montserrat:wght@300;400;500;600&family=Open+Sans:ital,wght@0,400;0,600;1,400&display=swap" rel="stylesheet">
<style>
:root{
  --ink:#333;
  --muted:#8a8a8a;
  --accent:#6a6e96;
  --accent-soft:#d7d8e6;
  --gold:#e6a01b;
  --page:#fff;
  --light:#f1f1f1;
  --footer:#333333;
  --footer-bar:#474747;
  --white:#fff;
}
*{box-sizing:border-box;margin:0;padding:0}
html,body{width:1200px;height:2332px;overflow:hidden}
body{position:relative;background:var(--page);font-family:"Open Sans",sans-serif;color:var(--ink)}
.abs{position:absolute}
a{color:inherit;text-decoration:none}

/* header */
.site-header{left:0;top:0;width:1200px;height:95px;background:var(--white)}
.brand{left:137px;top:30px;display:flex;align-items:center;gap:10px;font-family:"Montserrat",sans-serif;font-size:19px;font-weight:400;color:var(--accent)}
.brand-mark{width:26px;height:26px;border-radius:50%;background:var(--accent)}
.main-nav{left:492px;top:53px;display:flex;gap:0;font-family:"Montserrat",sans-serif;font-size:16px;color:#444}
.main-nav a{position:absolute;white-space:nowrap}
.main-nav .active{color:var(--accent)}
.nav-dot{left:506px;top:17px;width:22px;height:22px;border-radius:50%;background:var(--accent)}

/* hero */
.hero{left:0;top:95px;width:1200px;height:490px}
.hero-photo{position:absolute;inset:0;background:linear-gradient(100deg,#cfc2b0 0%,#d9cdbd 30%,#c8b9a4 55%,#b9a287 100%)}
.hero-floor{position:absolute;left:0;right:0;bottom:0;height:190px;background:linear-gradient(180deg,#c89c63,#b88547)}
.hero-title{left:143px;top:185px;color:var(--white);font-family:"Montserrat",sans-serif;font-weight:600;text-shadow:0 1px 3px rgba(0,0,0,.15)}
.hero-title .l1{display:block;font-size:48px;line-height:56px}
.hero-title .l2{display:block;font-size:37px;line-height:44px}
.optin{left:777px;top:105px;width:297px;height:268px;background:rgba(240,238,236,.93);padding:26px 25px}
.optin h2{font-family:"Montserrat",sans-serif;font-size:22px;font-weight:500;color:#222;margin-bottom:14px}
.optin .field{height:34px;border:1px solid #d4d4d4;background:#fff;font-size:12px;color:#888;padding:0 14px;line-height:32px;margin-bottom:8px}
.optin .btn{margin-top:12px;height:43px;background:var(--gold);color:#fff;font-family:"Montserrat",sans-serif;font-size:18px;text-align:center;line-height:43px}
.dots{display:flex;gap:5px}
.dots i{width:17px;height:17px;border-radius:50%;background:#fff;display:block}
.dots i.off{background:transparent;border:2px solid #fff}
.hero .dots{position:absolute;left:557px;top:426px}
.hero-wave{position:absolute;left:0;bottom:-1px}

/* features */
.feature{width:320px;text-align:center}
.feature svg{display:block;margin:0 auto}
.feature h3{font-family:"Montserrat",sans-serif;font-weight:400;font-size:20px;color:#333;margin-top:12px}
.feature p{font-size:13px;line-height:20px;color:var(--muted);margin:6px auto 0;width:290px;height:40px}
.pill{display:inline-block;border:1.5px solid var(--accent);border-radius:20px;color:var(--accent);font-size:13px;width:112px;height:34px;line-height:31px;text-align:center;margin-top:19px}

/* about */
.about{left:0;top:873px;width:1200px;height:374px;color:#fff;text-align:center}
.about-photo{position:absolute;inset:0;background:linear-gradient(180deg,#8e8fb5 0%,#7c80ab 45%,#5d6497 100%)}
.about-inner{position:relative;padding-top:60px}
.about h2{font-family:"Montserrat",sans-serif;font-weight:400;font-size:33px;margin-bottom:28px}
.about p{width:830px;margin:0 auto 10px;font-size:14px;line-height:23px}
.pill.light{border-color:#fff;color:#fff;width:125px;height:41px;line-height:38px;font-size:14px;margin-top:15px}

/* blogs */
.blogs{left:0;top:1247px;width:1200px;height:465px;background:var(--light)}
.blogs h2{position:absolute;left:0;width:1200px;top:48px;text-align:center;font-family:"Montserrat",sans-serif;font-weight:400;font-size:30px;color:#222}
.card{position:absolute;top:103px;width:303px;height:306px;background:#fff;box-shadow:0 1px 3px rgba(0,0,0,.12)}
.card .thumb{height:162px}
.card .body{padding:14px 25px 0}
.card h3{font-family:"Montserrat",sans-serif;font-weight:400;font-size:17px;line-height:22px;color:var(--accent);height:44px}
.card p{font-size:10.5px;line-height:17px;color:#888;margin-top:4px;height:50px;overflow:hidden}
.card .more{font-size:12px;color:#555;margin-top:8px;display:block}

/* testimonials */
.stories{left:0;top:1712px;width:1200px;height:318px;text-align:center}
.stories h2{margin-top:50px;font-family:"Montserrat",sans-serif;font-weight:400;font-size:30px;color:#222}
.quote{width:780px;margin:22px auto 0;font-style:italic;font-size:13px;line-height:24px;color:#666}
.qmark{position:absolute;top:90px;font-family:"Montserrat",sans-serif;font-weight:600;font-size:80px;line-height:1;color:#2c78b8}
.author{font-size:13px;color:#444;margin-top:10px}
.stories .dots{justify-content:center;margin-top:38px}
.stories .dots i{background:#bdbdbd;width:17px;height:17px}
.stories .dots i.off{background:transparent;border:2px solid #bdbdbd}

/* footer */
.site-footer{left:0;top:2030px;width:1200px;height:242px;background:var(--footer);color:#fff}
.fcol{position:absolute;top:50px;height:150px}
.fcol h4{font-family:"Montserrat",sans-serif;font-weight:400;font-size:17px;margin-bottom:14px}
.fcol li{list-style:none;font-size:12px;line-height:24px}
.fsep{position:absolute;top:48px;width:1px;height:154px;background:#4a4a4a}
.fcol .note{font-size:12px}
.fcol .email{width:207px;height:32px;background:#fff;color:#888;font-size:11px;padding-left:10px;line-height:32px;margin-top:10px}
.fcol .signup{width:97px;height:34px;background:var(--accent);color:#fff;text-align:center;line-height:34px;font-size:14px;margin-top:11px}
.social{display:flex;gap:18px;margin-top:12px;padding-left:8px}
.social i{width:16px;height:16px;border-radius:50%;background:#fff;display:block}
.footer-bar{left:0;top:2272px;width:1200px;height:60px;background:var(--footer-bar);color:#bbb;font-size:11px;text-align:center;line-height:60px}
</style>
</head>
<body>

<header class="site-header abs">
  <a class="brand abs" href="#"><span class="brand-mark"></span>Bright Fern Studies</a>
  <span class="nav-dot abs"></span>
  <nav class="main-nav abs">
    <a class="active" style="left:0">Home</a>
    <a style="left:83px">About</a>
    <a style="left:168px">Courses</a>
    <a style="left:270px">Blog</a>
    <a style="left:343px">Student Areas</a>
    <a style="left:490px">Contact</a>
  </nav>
</header>

<section class="hero abs">
  <div class="hero-photo" role="img" aria-label="Stacked smooth pebbles on a wooden board against a soft blurred background">
    <div class="hero-floor"></div>
  </div>
  <h1 class="hero-title abs"><span class="l1">Create your Ideal</span><span class="l2">Reiki Business</span></h1>
  <form class="optin abs">
    <h2>Stay Inspired</h2>
    <div class="field">First Name</div>
    <div class="field">Last Name</div>
    <div class="field">Email address</div>
    <div class="btn">Yes Count Me In</div>
  </form>
  <div class="dots"><i class="off"></i><i></i><i></i><i></i></div>
  <svg class="hero-wave" width="1200" height="60" viewBox="0 0 1200 60" preserveAspectRatio="none">
    <path d="M0 48 C300 0 520 10 760 28 C960 42 1100 30 1200 10 L1200 60 L0 60 Z" fill="#fff"/>
  </svg>
</section>

<section class="features">
  <div class="feature abs" style="left:124px;top:570px">
    <svg width="126" height="126" viewBox="0 0 126 126"><rect x="22" y="22" width="82" height="82" transform="rotate(45 63 63)" fill="#e4e4ec"/><rect x="28" y="28" width="70" height="70" transform="rotate(45 63 63)" fill="var(--accent)"/><path d="M63 48 C72 56 72 68 63 76 C54 68 54 56 63 48 Z M63 76 C52 76 44 70 42 60 C52 62 58 68 63 76 Z M63 76 C74 76 82 70 84 60 C74 62 68 68 63 76 Z" fill="none" stroke="#fff" stroke-width="1.6"/></svg>
    <h3>How Reiki Works</h3>
    <p>Reiki has been used for centuries to help individuals with physical and emotional</p>
    <a class="pill">Click here</a>
  </div>
  <div class="feature abs" style="left:433px;top:570px">
    <svg width="126" height="126" viewBox="0 0 126 126"><rect x="22" y="22" width="82" height="82" transform="rotate(45 63 63)" fill="#e4e4ec"/><rect x="28" y="28" width="70" height="70" transform="rotate(45 63 63)" fill="var(--accent)"/><path d="M63 42 C67 48 66 52 63 54 C60 52 59 48 63 42 Z" fill="#fff"/><rect x="57" y="57" width="12" height="20" fill="#fff"/><rect x="48" y="77" width="30" height="7" fill="#fff"/></svg>
    <h3>Our Courses</h3>
    <p>Learn how to use Reiki to help yourself and others.</p>
    <a class="pill">Click here</a>
  </div>
  <div class="feature abs" style="left:745px;top:570px">
    <svg width="126" height="126" viewBox="0 0 126 126"><rect x="22" y="22" width="82" height="82" transform="rotate(45 63 63)" fill="#e4e4ec"/><rect x="28" y="28" width="70" height="70" transform="rotate(45 63 63)" fill="var(--accent)"/><path d="M44 52 L63 58 L82 52 L82 76 L63 82 L44 76 Z M63 58 L63 82" fill="none" stroke="#fff" stroke-width="2"/></svg>
    <h3>Student Areas</h3>
    <p>Class aptent taciti sociosqu ad litora torquent per conubia nostra</p>
    <a class="pill">Click here</a>
  </div>
</section>

<section class="about abs">
  <div class="about-photo" role="img" aria-label="Person with raised arms standing at the shoreline at dusk, tinted in soft violet"></div>
  <div class="about-inner">
    <h2>About Bright Fern Studies</h2>
    <p>Thought to be centuries old and rediscovered in the late 1800's, Reiki (pronounced ray-key) is a healing and enlightenment system. Reiki can be translated into "Universal (Rei) Life Energy (Ki)". As a practitioner of Reiki, you attune your awareness to this energy and utilize it for the physical and emotional healing of self and others.</p>
    <p>Reiki is non-denominational and can be practiced by everyone, regardless of their religious and spiritual beliefs. Reiki can be performed hands-on in person or from a distance.</p>
    <a class="pill light">Read More</a>
  </div>
</section>

<section class="blogs abs">
  <h2>Our Blogs</h2>
  <article class="card" style="left:133px">
    <div class="thumb" role="img" aria-label="Balanced stones at sunset in warm orange light" style="background:linear-gradient(180deg,#f3a53a,#c9671a 60%,#5a3012)"></div>
    <div class="body"><h3>How to handle Reiki client no-shows</h3><p>How do you deal with patient no-shows? And then when the same patient wants to reschedule</p><a class="more">READ MORE</a></div>
  </article>
  <article class="card" style="left:449px">
    <div class="thumb" role="img" aria-label="Relaxing spa treatment with towels and flowers" style="background:linear-gradient(90deg,#9a6a3c,#e9d6c4 50%,#6f8e6a)"></div>
    <div class="body"><h3>Friday FAQ's July 1st</h3><p>I have a question about the part when performing Reiki and the hands are going through those hand positions for 3-5 minutes at a time...within those</p><a class="more">READ MORE</a></div>
  </article>
  <article class="card" style="left:766px">
    <div class="thumb" role="img" aria-label="Yoga stretch on a bright beach by the sea" style="background:linear-gradient(180deg,#eef0a8,#d6e4a0 55%,#7fb3b8)"></div>
    <div class="body"><h3>How to handle Reiki client no-shows</h3><p>How do you deal with patient no-shows? And then when the same patient wants to reschedule</p><a class="more">READ MORE</a></div>
  </article>
</section>

<section class="stories abs">
  <h2>Success Stories</h2>
  <span class="qmark" style="left:165px">&ldquo;</span>
  <span class="qmark" style="left:1000px">&rdquo;</span>
  <p class="quote">I was drawn to this course with the desire to heal family, friends and pets and this course has given me that ability and more. With it, Reiki has healed me on many levels and given me insight into my own spirituality and to what is possible. The continued contact with Mara Ellison on the Lumen group page as well as input and questions and answers from other students</p>
  <p class="author">By Author Name</p>
  <div class="dots"><i class="off"></i><i></i><i></i><i></i></div>
</section>

<footer class="site-footer abs">
  <div class="fcol" style="left:143px"><h4>INFORMATION</h4><ul><li>Home</li><li>About Us</li><li>Our Coures</li><li>Admission</li></ul></div>
  <span class="fsep" style="left:281px"></span>
  <div class="fcol" style="left:321px"><h4>COURSES</h4><ul><li>Mauris vel lacus</li><li>Aitae felis</li><li>Vestibulum</li><li>volutpat imperdiet</li></ul></div>
  <span class="fsep" style="left:448px"></span>
  <div class="fcol" style="left:488px"><h4>RESOURCES</h4><ul><li>Student Stories</li><li>Our Management</li><li>Our Teachers</li><li>Sitemap</li></ul></div>
  <span class="fsep" style="left:633px"></span>
  <div class="fcol" style="left:681px"><h4>SUPPORT</h4><ul><li>FAQ</li><li>Term of Use</li><li>Privacy Policy</li><li>Contact</li></ul></div>
  <span class="fsep" style="left:817px"></span>
  <div class="fcol" style="left:862px"><h4>JOB ALERT NOW</h4><p class="note">Please Sign up here for updates</p><div class="email">Email address</div><div class="signup">Sign Up</div><div class="social"><i></i><i></i><i></i><i></i></div></div>
</footer>
<div class="footer-bar abs">© 2016 Company Name &nbsp;All right reserved &nbsp;Term of Use</div>

</body>
</html>
```